High Tech Real Estate Startup needs a business card

We are developing an innovative real estate marketing product based around advanced search and virtual reality.

We talk to people, we need business cards.

Target Market(s)

The target market is technology professionals and realtors.

Contact Information for Business Card

The information to be included will include

Name
Title
Phone Number
E-mail Address
www.zelquin.com

It should use simple iconography for each one of those fields.

Font styles to use
Other font styles liked:
• Co, Jubilat, Avenir

Colors

Designer to choose colors to be used in the design.

Requirements
Must have
• Clean aesthetic,
• Good use of negative space.
• It should use our company logo, shown in the attached file. It is able to use the negative of that logo (coloured font and white background) and I have attached other acceptable accent colours in a swatch file.
Should not have
• Should not be too busy
• No extraneous text (slogans, tag lines etc)

```html
<!DOCTYPE html>
<html lang="en">
<head>
<meta charset="utf-8">
<title>Zelquin Business Card</title>
<link rel="stylesheet" href="https://fonts.googleapis.com/css2?family=Nunito+Sans:wght@400;600&family=Roboto+Condensed:wght@400;700&display=swap">
<style>
  :root {
    --teal: #04b7bf;
    --teal-dark: #02a9b1;
    --white: #ffffff;
    --ink: #3a3a3a;
    --backdrop: #e9ecec;
  }
  * { margin: 0; padding: 0; box-sizing: border-box; }
  html, body { width: 1200px; height: 911px; overflow: hidden; }
  body {
    background: var(--backdrop);
    position: relative;
    font-family: "Nunito Sans", sans-serif;
  }
  .card {
    position: absolute;
    width: 560px;
    height: 320px;
    background: var(--teal);
    overflow: hidden;
    box-shadow: 0 10px 30px rgba(0,0,0,0.18);
  }
  .card--front { left: 80px; top: 90px; }
  .card--back { left: 560px; top: 500px; }

  .front-wave { position: absolute; inset: 0; width: 100%; height: 100%; }

  .brand-name {
    position: absolute;
    color: var(--white);
    font-family: "Nunito Sans", sans-serif;
    font-weight: 600;
    letter-spacing: 4px;
    line-height: 1;
  }
  .card--front .brand-name { left: 40px; bottom: 44px; font-size: 50px; }
  .card--back .brand-name {
    left: 0; right: 0; top: 112px;
    text-align: center; font-size: 66px; letter-spacing: 6px;
  }
  .back-web {
    position: absolute;
    left: 0; right: 0; top: 208px;
    text-align: center;
    color: var(--white);
    font-family: "Nunito Sans", sans-serif;
    font-size: 13px;
    letter-spacing: 6px;
  }

  .contact {
    position: absolute;
    right: 34px;
    top: 56px;
    text-align: right;
    font-family: "Roboto Condensed", sans-serif;
  }
  .contact__name {
    color: var(--teal);
    font-weight: 700;
    font-size: 22px;
    letter-spacing: 0.5px;
  }
  .contact__title {
    color: var(--ink);
    font-size: 15px;
    margin-top: 2px;
    margin-bottom: 16px;
  }
  .contact__row {
    display: flex;
    justify-content: flex-end;
    align-items: center;
    gap: 8px;
    color: var(--ink);
    font-size: 14px;
    line-height: 22px;
  }
  .contact__icon { width: 13px; height: 13px; flex: none; }
</style>
</head>
<body>

  <section class="card card--front" aria-label="Business card front">
    <svg class="front-wave" viewBox="0 0 560 320" preserveAspectRatio="none">
      <path d="M560 0 L560 320 L300 320 C360 250 330 170 300 110 C275 60 300 10 340 0 Z" fill="var(--white)"/>
      <path d="M330 0 C288 12 266 60 292 112 C322 172 348 250 290 320" fill="none" stroke="var(--white)" stroke-width="3"/>
    </svg>
    <div class="brand-name">ZELQUIN</div>
    <div class="contact">
      <div class="contact__name">DANA WHITFIELD</div>
      <div class="contact__title">CEO/FOUNDER</div>
      <div class="contact__row">
        <span>555 014 2938</span>
        <svg class="contact__icon" viewBox="0 0 16 16"><path d="M4 1 L6.5 4.5 L5 6.5 C6 8.5 7.5 10 9.5 11 L11.5 9.5 L15 12 L13 15 C7 14.5 1.5 9 1 3 Z" fill="var(--teal)"/></svg>
      </div>
      <div class="contact__row">
        <span>dana@zelquin.com</span>
        <svg class="contact__icon" viewBox="0 0 16 16"><rect x="0" y="2" width="16" height="12" rx="2" fill="var(--teal)"/><path d="M2 4.5 L8 9 L14 4.5" fill="none" stroke="var(--white)" stroke-width="1.5"/></svg>
      </div>
      <div class="contact__row">
        <span>www.zelquin.com</span>
        <svg class="contact__icon" viewBox="0 0 16 16"><circle cx="8" cy="8" r="8" fill="var(--teal)"/><ellipse cx="8" cy="8" rx="3" ry="6.5" fill="none" stroke="var(--white)" stroke-width="1.2"/><path d="M1.5 8 H14.5" stroke="var(--white)" stroke-width="1.2"/></svg>
      </div>
    </div>
  </section>

  <section class="card card--back" aria-label="Business card back">
    <div class="brand-name">ZELQUIN</div>
    <div class="back-web">WWW.ZELQUIN.COM</div>
  </section>

</body>
</html>
```